Lumora Systems New Website - IT Infrastructure | Smart Cabinet | Micro Data Center

We're an IT SI providing Server Room Design & Build | All-in-One Rack & Smart Cabinet | Structured Cabling | IT Relocation | Maintenance. Old website can be found at www.lumorasys.com.hk. We'd like a brand new wix website which is modern, minimalist, interactive with some animation. Website content will be mostly static and include our service, our project, news and events, about us, contacts, blogs, partners and brands, etc.

reference sites:
We'd like to see more designs referring to below

https://www.pixelvane.example/design/41736205
https://www.pixelvane.example/design/41892417
https://velbrinn.example/

Animation (scrolling effect) referring to
https://velbrinn.example/intelligence/smart-office-room/
Updates

we'd like below style.

Designs look the same

Target Market(s)

Commercials in HK

Industry/Entity Type

IT, Technology, Data Center

Coding

Coded - Design and coding required

Font styles to use
Sans Serif

Requirements
Must have
• CMS, Some Interactive Elements/ Graphics

```html
<!DOCTYPE html>
<html lang="en">
<head>
<meta charset="utf-8">
<title>Lumora Systems — IT Infrastructure</title>
<link rel="stylesheet" href="https://fonts.googleapis.com/css2?family=Poppins:wght@400;500;600;700&family=Roboto:wght@400;500;700&display=swap">
<style>
:root{
  --orange:#f57c1f;
  --navy:#173a52;
  --navy-deep:#0f2a3d;
  --ink:#2b3640;
  --muted:#8a8f96;
  --light:#f5f6f7;
  --line:#e4e6e8;
  --footer:#222426;
  --white:#fff;
  --play:#2fb57a;
}
*{margin:0;padding:0;box-sizing:border-box}
html,body{width:1200px;height:5266px;overflow:hidden}
body{position:relative;font-family:Roboto,Arial,sans-serif;color:var(--ink);background:var(--white)}
.abs{position:absolute}
h1,h2,h3,h4{font-family:Poppins,Arial,sans-serif}
.sec-title{position:absolute;left:0;width:1200px;text-align:center;font-size:30px;font-weight:600;color:var(--navy)}
.sec-lead{position:absolute;left:330px;width:540px;text-align:center;font-size:12px;line-height:22px;color:var(--muted)}
.btn{position:absolute;display:flex;align-items:center;justify-content:center;gap:10px;background:var(--orange);color:#fff;font-family:Poppins,sans-serif;font-weight:600;font-size:12px;border-radius:4px}
.photo{position:absolute}

/* header */
.topbar{left:450px;top:0;width:750px;height:33px;background:var(--navy-deep);color:#fff;font-size:9px;display:flex;align-items:center}
.topbar span{position:absolute;white-space:nowrap}
.navbar{left:0;top:33px;width:1200px;height:45px;background:#fff}
.brand{display:flex;align-items:center;gap:8px;font-family:Poppins,sans-serif;font-weight:600;font-size:18px;color:var(--orange);white-space:nowrap}
.brand i{width:22px;height:22px;background:var(--orange);border-radius:4px;display:block}
.nav a{position:absolute;top:17px;font-size:11px;color:#555;text-decoration:none}
.nav a.on{color:var(--navy);font-weight:700}

/* hero */
.hero{left:0;top:78px;width:1200px;height:633px;background:linear-gradient(100deg,#0d1e2c 0%,#2b4a62 40%,#46667e 60%,#1a2f40 100%)}
.hero .eyebrow{left:110px;top:196px;color:#fff;font-size:12px;display:flex;align-items:center;gap:12px}
.hero .eyebrow b{display:block;width:45px;height:1px;background:#fff;font-weight:400}
.hero h1{left:110px;top:246px;color:#fff;font-size:40px;line-height:58px;font-weight:700}
.hero p{left:110px;top:400px;width:400px;color:#fff;font-size:12px;line-height:22px}

/* why */
.why{left:0;top:711px;width:1200px;height:607px;background:var(--light)}
.card{position:absolute;top:260px;width:235px;height:215px;background:#fff;border:1px solid var(--line);border-radius:4px;text-align:center;box-shadow:0 3px 10px rgba(0,0,0,.05)}
.card svg{margin-top:32px}
.card h3{font-size:16px;font-weight:600;color:var(--navy);line-height:25px;margin-top:14px}
.card p{font-size:12px;line-height:22px;color:var(--muted);margin-top:4px}
.card.dark{background:var(--navy);border-color:var(--navy)}
.card.dark h3,.card.dark p{color:#fff}

/* future */
.future{left:0;top:1318px;width:1200px;height:516px;background:var(--light)}
.future .band{left:282px;top:0;width:918px;height:473px;background:var(--navy)}
.future h2{left:634px;top:96px;color:#fff;font-size:30px;font-weight:600;white-space:nowrap}
.future p{left:632px;width:430px;color:#fff;font-size:12px;line-height:22px}

/* services */
.services{left:0;top:1834px;width:1200px;height:678px;background:var(--light)}
.svc{position:absolute;top:230px;width:321px;height:379px}
.svc .img{left:0;top:0;width:321px;height:236px}
.svc .box{left:20px;top:178px;width:281px;height:201px;background:#fff;padding:26px 30px 26px 38px;box-shadow:0 4px 14px rgba(0,0,0,.08)}
.svc .box h3{font-size:19px;font-weight:600;color:var(--navy);white-space:nowrap}
.svc .box p{font-size:12px;line-height:21px;color:var(--muted);margin-top:8px}
.svc .box .more{font-size:11px;font-weight:700;color:var(--orange);margin-top:12px;font-family:Poppins,sans-serif}
.svc.dark .box{background:var(--navy)}
.svc.dark .box h3,.svc.dark .box p,.svc.dark .box .more{color:#fff}

/* cta */
.cta{left:0;top:2512px;width:1200px;height:294px;background:linear-gradient(100deg,#0b1a26,#1c3a52 50%,#0e2231)}
.cta .phone{left:0;top:50px;width:1200px;text-align:center;color:#fff;font-family:Poppins,sans-serif;font-size:20px;font-weight:600}
.cta h2{left:0;top:88px;width:1200px;text-align:center;color:#fff;font-size:29px;font-weight:600}
.cta p{left:330px;top:142px;width:540px;text-align:center;color:#fff;font-size:12px;line-height:22px}
.cta .outline{left:519px;top:209px;width:168px;height:43px;border:1px solid #fff;border-radius:4px;color:#fff;font-family:Poppins,sans-serif;font-size:12px;font-weight:600;display:flex;align-items:center;justify-content:center}

/* projects */
.projects{left:0;top:2806px;width:1200px;height:669px;background:var(--light)}
.play{left:555px;top:382px;width:74px;height:74px;border-radius:50%;background:var(--play);display:flex;align-items:center;justify-content:center}
.proj-cap{left:390px;top:548px;width:420px;color:#fff;font-size:16px;line-height:24px}

/* reviews */
.reviews{left:0;top:3475px;width:1200px;height:541px;background:#fff}
.review{position:absolute;top:190px;width:494px;height:253px;background:var(--light)}
.review .rule{left:63px;top:46px;width:1px;height:161px;background:#c9ccd0}
.review .quote{left:41px;top:104px;width:46px;height:46px;border-radius:50%;background:var(--orange);border:4px solid #fff;box-shadow:0 0 0 1px var(--orange);display:flex;align-items:center;justify-content:center;color:#fff;font-family:Poppins,sans-serif;font-weight:700;font-size:26px}
.review .stars{left:114px;top:40px;color:var(--orange);font-size:16px;letter-spacing:3px}
.review p{left:114px;top:82px;width:350px;font-size:12px;line-height:22px;color:var(--muted)}
.review h4{left:114px;top:170px;font-size:16px;font-weight:600;color:var(--ink)}
.review .loc{left:114px;top:196px;font-size:11px;color:var(--muted)}
.review .avatar{left:402px;top:164px;width:58px;height:58px;border-radius:50%;background:linear-gradient(135deg,#d9c7b7,#9e8878)}
.dots{left:565px;top:492px;display:flex;gap:10px}
.dots i{width:9px;height:9px;border-radius:50%;background:var(--orange);display:block}
.dots i.off{background:#fff;border:1px solid var(--orange)}

/* contact */
.contact{left:0;top:4016px;width:1200px;height:798px;background:var(--light)}
.c-box{left:90px;top:203px;width:1018px;height:462px;background:#fff;box-shadow:0 4px 16px rgba(0,0,0,.06)}
.c-info{left:0;top:0;width:509px;height:462px;background:linear-gradient(90deg,rgba(23,58,82,.97),rgba(36,72,98,.85)),#3b5b73;color:#fff;padding:70px 0 0 86px}
.c-info h4{font-size:16px;font-weight:600}
.c-info .call{font-family:Poppins,sans-serif;font-size:20px;font-weight:600;margin-top:18px}
.c-info .mail{font-size:11px;font-weight:700;margin-top:6px}
.c-info .blk{font-size:11px;font-weight:700;line-height:18px;margin-top:28px}
.c-info .soc{display:flex;gap:10px;margin-top:50px}
.c-info .soc i{width:30px;height:30px;border-radius:50%;border:1px solid rgba(255,255,255,.5);display:block}
.c-info .soc i.f{background:#fff}
.c-form h4{position:absolute;left:597px;top:62px;font-size:16px;font-weight:600;color:var(--navy)}
.field{position:absolute;left:597px;width:331px;height:27px;background:var(--light);font-size:9px;color:#777;padding:8px 14px}
.submit{left:597px;top:374px;width:110px;height:34px;font-size:11px;border-radius:3px}

/* footer */
.footer{left:0;top:4814px;width:1200px;height:452px;background:var(--footer);color:#fff}
.info-bar{left:65px;top:4763px;width:1071px;height:102px;background:var(--orange);border-radius:6px;color:#fff}
.info-item{position:absolute;top:0;height:102px;display:flex;align-items:center;gap:22px}
.info-item h4{font-size:17px;font-weight:600}
.info-item span{font-size:12px;white-space:nowrap}
.f-col h4{font-size:17px;font-weight:600}
.f-text{font-size:12px;line-height:32px}
.f-links a{position:absolute;font-size:12px;color:#fff;text-decoration:underline}
.sub-in{left:797px;top:259px;width:339px;height:52px;background:#fff;border-radius:4px;color:#666;font-size:12px;padding:18px 20px}
.sub-go{left:1073px;top:259px;width:63px;height:52px;background:var(--orange);border-radius:0 4px 4px 0;display:flex;align-items:center;justify-content:center}
.bottom{left:0;top:384px;width:1200px;height:68px;border-top:1px solid #3a3d40}
.f-brand{left:65px;top:0;width:172px;height:68px;background:var(--orange);display:flex;align-items:center;justify-content:center;gap:7px;font-family:Poppins,sans-serif;font-weight:600;font-size:15px;color:#fff;white-space:nowrap}
.f-brand i{width:16px;height:16px;background:#fff;border-radius:3px;display:block}
.soc-cell{position:absolute;top:0;width:58px;height:68px;border-left:1px solid #3a3d40;display:flex;align-items:center;justify-content:center}
.soc-cell i{width:12px;height:12px;border-radius:50%;background:#5c6064;display:block}
</style>
</head>
<body>

<!-- header -->
<div class="abs topbar">
  <span style="left:16px">&#9679; 18 Harbour Lane, Kowloon</span>
  <span style="left:243px">FOLLOW US &nbsp; &#9679; &#9679; &#9679;</span>
  <span style="left:408px">MAKE APPOINTMENT</span>
</div>
<header class="abs navbar">
  <div class="abs brand" style="left:118px;top:9px"><i></i>Lumora Systems</div>
  <nav class="nav">
    <a class="on" style="left:403px">Home</a>
    <a style="left:485px">About Us</a>
    <a style="left:585px">Services</a>
    <a style="left:685px">Our Team</a>
    <a style="left:797px">Projects</a>
    <a style="left:885px">Contact Us</a>
  </nav>
</header>

<!-- hero -->
<section class="abs hero" role="img" aria-label="Photo of a server room aisle with glowing racks">
  <div class="abs eyebrow">On the other hand <b></b></div>
  <h1 class="abs">Pioneering Tomorrow's<br>Digital Landscape</h1>
  <p class="abs">Lorem ipsum dolor sit amet, consectetur adipiscing elit, sed d o eiusmod temp dipiscing elit, sed d</p>
  <div class="btn" style="left:110px;top:480px;width:168px;height:43px">Contact Us</div>
</section>

<!-- why we are the best -->
<section class="abs why">
  <h2 class="sec-title" style="top:130px">Why we are the best</h2>
  <p class="sec-lead" style="top:185px">Lorem ipsum dolor sit amet, consectetur adipiscing elit, sed do eiusmod tempor incididunt ut labore et dolore magna aliqua. Ut enim ad min</p>

  <div class="card" style="left:92px">
    <svg width="40" height="40" viewBox="0 0 40 40" fill="none" stroke="#f57c1f" stroke-width="2"><path d="M20 6l4 8 9 1-7 6 2 9-8-5-8 5 2-9-7-6 9-1z"/><path d="M12 34h16"/></svg>
    <h3>Personalized<br>Approach</h3>
    <p>Lorem ipsum dolor sit amet,<br>consectetur adipiscing</p>
  </div>
  <div class="card dark" style="left:352px">
    <svg width="40" height="40" viewBox="0 0 40 40" fill="none" stroke="#f57c1f" stroke-width="2"><circle cx="20" cy="14" r="7"/><path d="M14 20l-5 14 6-3 3 5M26 20l5 14-6-3-3 5"/></svg>
    <h3>Proven<br>Track Record</h3>
    <p>Lorem ipsum dolor sit amet,<br>consectetur adipiscing</p>
  </div>
  <div class="card" style="left:612px">
    <svg width="40" height="40" viewBox="0 0 40 40" fill="none" stroke="#f57c1f" stroke-width="2"><circle cx="20" cy="20" r="13"/><path d="M20 12v9l5 4"/></svg>
    <h3>Compliance and<br>Certifications</h3>
    <p>Lorem ipsum dolor sit amet,<br>consectetur adipiscing</p>
  </div>
  <div class="card" style="left:872px">
    <svg width="40" height="40" viewBox="0 0 40 40" fill="none" stroke="#f57c1f" stroke-width="2"><circle cx="20" cy="13" r="7"/><path d="M7 35c1-8 6-12 13-12s12 4 13 12z"/></svg>
    <h3>Proactive<br>Maintenance</h3>
    <p>Lorem ipsum dolor sit amet,<br>consectetur adipiscing</p>
  </div>

  <div class="btn" style="left:523px;top:515px;width:168px;height:43px">Meer Leren</div>
</section>

<!-- future-ready -->
<section class="abs future">
  <div class="abs band"></div>
  <div class="photo" style="left:0;top:70px;width:583px;height:446px;background:linear-gradient(110deg,#101c26,#3d5466 45%,#7c8fa0 60%,#1d2c38)" role="img" aria-label="Photo of an engineer with a laptop beside open server racks"></div>
  <h2 class="abs">Future-Ready Data Foundations</h2>
  <p class="abs" style="top:148px">Lorem ipsum dolor sit amet, consectetur adipiscing elit, sed do eiusmod tempor incididunt ut labore et dolore magna aliqua. Ut e nim ad min veniam, quis nostrud ex.</p>
  <p class="abs" style="top:222px">Lorem ipsum dolor sit amet, consectetur adipiscing elit, sed do eiusmod tempor incididunt ut labore et dolore magna aliqua. Ut e nim ad min veniam, quis nostrud ex. et dolore magna aliqua. Ut e nim ad min veniam, quis nostrud ex.</p>
  <div class="btn" style="left:632px;top:334px;width:155px;height:45px;font-size:14px">Meer Leren
    <svg width="18" height="12" viewBox="0 0 18 12" fill="none" stroke="#fff" stroke-width="1.8"><path d="M0 6h16M11 1l5 5-5 5"/></svg>
  </div>
</section>

<!-- services -->
<section class="abs services">
  <h2 class="sec-title" style="top:78px">Our Services</h2>
  <p class="sec-lead" style="top:130px">Lorem ipsum dolor sit amet, consectetur adipiscing elit, sed do eiusmod tempor incididunt ut labore et dolore magna aliqua. Ut enim ad min</p>

  <div class="svc" style="left:92px">
    <div class="photo img" style="background:linear-gradient(135deg,#2b3b48,#6f7f8c 60%,#3a4b58)" role="img" aria-label="Photo of a smiling technician in a data centre"></div>
    <div class="abs box"><h3>Data Centre Building</h3><p>Lorem ipsum dolor sit amet, cons ectetur adipiscing elit, sed do eiu smod tempor incididunt ut labore et dolore magna aliqua.</p><div class="more">MEER LEREN</div></div>
  </div>
  <div class="svc dark" style="left:439px">
    <div class="photo img" style="background:linear-gradient(135deg,#1d2a35,#55636f 55%,#9aa4ad)" role="img" aria-label="Photo of a technician on a phone call in a server room"></div>
    <div class="abs box"><h3>Structured Cabling</h3><p>Lorem ipsum dolor sit amet, cons ectetur adipiscing elit, sed do eiu smod tempor incididunt ut labore et dolore magna aliqua.</p><div class="more">MEER LEREN</div></div>
  </div>
  <div class="svc" style="left:787px">
    <div class="photo img" style="background:linear-gradient(135deg,#3a4752,#8a97a2 50%,#2a3641)" role="img" aria-label="Photo of an engineer working at a rack with network cables"></div>
    <div class="abs box"><h3>Audio-Visual</h3><p>Lorem ipsum dolor sit amet, cons ectetur adipiscing elit, sed do eiu smod tempor incididunt ut labore et dolore magna aliqua.</p><div class="more">MEER LEREN</div></div>
  </div>
</section>

<!-- call to action -->
<section class="abs cta" role="img" aria-label="Dark photo of server racks behind the call to action">
  <div class="abs phone">852-3918-4402</div>
  <h2 class="abs">Efficiency Redefined, Data Perfected</h2>
  <p class="abs">Lorem ipsum dolor sit amet, consectetur adipiscing elit, sed do eiusmod tempor incididunt ut labore et dolore magna aliqua. Ut enim ad min</p>
  <div class="abs outline">Contact Us</div>
</section>

<!-- projects -->
<section class="abs projects">
  <h2 class="sec-title" style="top:78px">Our Recent Projects</h2>
  <p class="sec-lead" style="top:130px">Lorem ipsum dolor sit amet, consectetur adipiscing elit, sed do eiusmod tempor incididunt ut labore et dolore magna aliqua. Ut enim ad min</p>
  <div class="photo" style="left:92px;top:213px;width:235px;height:376px;clip-path:polygon(0 12%,100% 0,100% 100%,0 88%);background:linear-gradient(135deg,#7d95ad,#c4d2df 50%,#6e859b)" role="img" aria-label="Photo of server hardware close-up"></div>
  <div class="photo" style="left:354px;top:213px;width:494px;height:376px;background:linear-gradient(90deg,#1a2432,#44566c 45%,#c8ced4 70%,#3b4b5d)" role="img" aria-label="Photo of a long data centre aisle between server racks"></div>
  <div class="abs play"><svg width="26" height="30" viewBox="0 0 26 30"><path d="M2 1l23 14L2 29z" fill="#fff"/></svg></div>
  <p class="abs proj-cap">Lorem ipsum dolor sit amet, consecteturipsum<br>dolor sit amet, consectetur</p>
  <div class="photo" style="left:873px;top:213px;width:233px;height:376px;clip-path:polygon(0 0,100% 12%,100% 88%,0 100%);background:linear-gradient(135deg,#2a3a5a,#5a72a0 50%,#1f2d48)" role="img" aria-label="Photo of blue-lit server racks"></div>
</section>

<!-- reviews -->
<section class="abs reviews">
  <h2 class="sec-title" style="top:60px">Client Reviews</h2>
  <p class="sec-lead" style="top:112px">Lorem ipsum dolor sit amet, consectetur adipiscing elit, sed do eiusmod tempor incididunt ut labore et dolore magna aliqua. Ut enim ad min</p>

  <div class="review" style="left:90px">
    <div class="abs rule"></div>
    <div class="abs quote">&#8220;</div>
    <div class="abs stars">&#9733;&#9733;&#9733;&#9733;&#9733;</div>
    <p class="abs">Lorem ipsum dolor sit amet, consectetur adipiscing elit, sed do eiusmod tempor incididunt ut labore et d olore magna aliqua.</p>
    <h4 class="abs">Maren Holt</h4>
    <div class="abs loc">Green Valley</div>
    <div class="abs avatar" role="img" aria-label="Client portrait"></div>
  </div>
  <div class="review" style="left:610px">
    <div class="abs rule"></div>
    <div class="abs quote">&#8220;</div>
    <div class="abs stars">&#9733;&#9733;&#9733;&#9733;&#9733;</div>
    <p class="abs">Lorem ipsum dolor sit amet, consectetur adipiscing elit, sed do eiusmod tempor incididunt ut labore et d olore magna aliqua.</p>
    <h4 class="abs">Maren Holt</h4>
    <div class="abs loc">Green Valley</div>
    <div class="abs avatar" role="img" aria-label="Client portrait"></div>
  </div>

  <div class="abs dots"><i></i><i></i><i class="off"></i><i></i></div>
</section>

<!-- contact -->
<section class="abs contact">
  <h2 class="sec-title" style="top:60px">Feel free to contact us</h2>
  <p class="sec-lead" style="top:112px">Lorem ipsum dolor sit amet, consectetur adipiscing elit, sed do eiusmod tempor incididunt ut labore et dolore magna aliqua. Ut enim ad min</p>

  <div class="abs c-box">
    <div class="abs c-info" role="img" aria-label="Photo of a support agent with a headset, tinted navy">
      <h4>CONTACT US</h4>
      <div class="call">Call: 2739 5184</div>
      <div class="mail">hello@lumorasys.hk</div>
      <div class="blk">Address:<br>UNIT 5, KWUN TONG<br>18 Harbour Lane</div>
      <div class="blk">Operating Hours<br>Monday to Saturday: 9:00 - 18:00<br>Sunday: Closed</div>
      <div class="soc"><i></i><i class="f"></i><i></i><i></i></div>
    </div>
    <div class="c-form">
      <h4>FREE CONSULTATION</h4>
      <div class="field" style="top:110px">Your Name</div>
      <div class="field" style="top:159px">Email</div>
      <div class="field" style="top:208px">Phone</div>
      <div class="field" style="top:260px;height:92px">Message</div>
      <div class="btn submit">SUBMIT</div>
    </div>
  </div>
</section>

<!-- footer -->
<footer class="abs footer">
  <div class="abs f-col" style="left:65px;top:137px">
    <h4>About Company</h4>
    <div style="width:32px;height:2px;background:var(--orange);margin-top:14px"></div>
    <p class="f-text" style="width:320px;margin-top:16px">Lorem ipsum dolor sit amet, consectetur adipis cing elit, sed do eiusmod tempor incididunt ut labore et dolore magna aliqua.</p>
    <p style="color:var(--orange);font-size:13px;text-decoration:underline;margin-top:6px">Read More</p>
  </div>
  <div class="abs f-col" style="left:433px;top:137px">
    <h4>Useful Links</h4>
    <div style="width:32px;height:2px;background:var(--orange);margin-top:14px"></div>
  </div>
  <div class="f-links">
    <a style="left:433px;top:206px">About Us</a>
    <a style="left:433px;top:239px">Projects</a>
    <a style="left:433px;top:272px">Blog</a>
    <a style="left:433px;top:305px">Contact Us</a>
    <a style="left:609px;top:206px">Services</a>
    <a style="left:609px;top:239px">Shop</a>
    <a style="left:609px;top:272px">Privacy Policy</a>
    <a style="left:609px;top:305px">Help Desk</a>
  </div>
  <div class="abs f-col" style="left:797px;top:137px">
    <h4>Subscribe</h4>
    <p style="font-size:13px;line-height:24px;width:340px;margin-top:30px">If you have any questions, Subscribe to our newsletter to know more</p>
  </div>
  <div class="abs sub-in">Email</div>
  <div class="abs sub-go"><svg width="12" height="18" viewBox="0 0 12 18" fill="none" stroke="#fff" stroke-width="2.4"><path d="M2 2l7 7-7 7"/></svg></div>

  <div class="abs bottom">
    <div class="abs f-brand"><i></i>Lumora Systems</div>
    <div class="soc-cell" style="left:905px"><i></i></div>
    <div class="soc-cell" style="left:963px"><i></i></div>
    <div class="soc-cell" style="left:1021px"><i></i></div>
    <div class="soc-cell" style="left:1079px;border-right:1px solid #3a3d40"><i></i></div>
  </div>
</footer>

<div class="abs info-bar">
  <div class="info-item" style="left:40px">
    <svg width="52" height="48" viewBox="0 0 52 48" fill="none" stroke="#fff" stroke-width="2"><path d="M26 4a10 10 0 0 1 10 10c0 8-10 18-10 18S16 22 16 14A10 10 0 0 1 26 4z"/><circle cx="26" cy="14" r="4"/><path d="M4 44l10-14h24l10 14z"/></svg>
    <div><h4>Location</h4><span>18 Harbour Lane, HK</span></div>
  </div>
  <svg class="abs" style="left:345px;top:0" width="28" height="102" viewBox="0 0 28 102" fill="none" stroke="#fff" stroke-width="2"><path d="M2 0l22 51L2 102"/></svg>
  <div class="info-item" style="left:405px">
    <svg width="48" height="50" viewBox="0 0 48 50" fill="none" stroke="#fff" stroke-width="2"><rect x="6" y="4" width="22" height="42" rx="3"/><path d="M14 40h6M34 16c4 3 4 12 0 16M39 12c6 5 6 19 0 24"/></svg>
    <div><h4>Telephone</h4><span>+852 3918 4402</span></div>
  </div>
  <svg class="abs" style="left:700px;top:0" width="28" height="102" viewBox="0 0 28 102" fill="none" stroke="#fff" stroke-width="2"><path d="M2 0l22 51L2 102"/></svg>
  <div class="info-item" style="left:755px">
    <svg width="50" height="48" viewBox="0 0 50 48" fill="none" stroke="#fff" stroke-width="2"><path d="M4 18l21-14 21 14v26H4z"/><path d="M4 18l21 14 21-14M12 12h26v12"/></svg>
    <div><h4>Email</h4><span>hello@lumorasys.hk</span></div>
  </div>
</div>

</body>
</html>
```